RW Holloway LLC Business Card - Civil Engineering & Consulting Firm

We need a Business Card that is elegant, and masculine.  It is our Professional Civil Engineering & Consulting Company located in San Antonio TX (Not s construction or builder firm- no gears & no tool images please). We provide civil engineering services including  commercial site plans, grading and drainage plans, utility plans, hydraulics and hydrology, land planning, utility coordination, and other general civil engineering services related to commercial and residential development.
We have 2 existing Logos. We would like to convey reliability, strength, trustworthiness and attention to detail.  Blues and orange tones as per logo We are OK with the use of a darker blue in the mix.  We have 2 logo versions - Full Company Name Logo to go on the back of card, & Small Icon Logo for the front w/ personal Info.

Target Market(s)
Architects, Real Estate Developers, Other Strctural Engineers, Surveyers, General Contractors
Industry/Entity Type
Professional Civil Engineering
Contact Information for Business Card
Name, Position, Address, Cell & Office #, email, and company website
Font styles to use
Other font styles liked:
- Avian
Requirements
Should not have
- No Tools, No Gears, no Cranes, or Construction Equipment.

```html
<!DOCTYPE html>
<html lang="en">
<head>
<meta charset="utf-8">
<title>RW Holloway LLC – Business Card</title>
<link rel="stylesheet" href="https://fonts.googleapis.com/css2?family=Montserrat:wght@400;500;700&family=Josefin+Sans:wght@300;400&display=swap">
<style>
  :root{
    --stage:#1d1d1f;
    --sky:#7aa9d4;
    --sky-soft:#8fb0cc;
    --amber:#ee9633;
    --amber-soft:#d9944f;
    --paper:#ffffff;
    --paper-shade:#eeeeee;
    --ink:#1e1e1e;
    --steel:#a8a39a;
  }
  *{box-sizing:border-box;margin:0;padding:0}
  html,body{width:1200px;height:900px;overflow:hidden}
  body{background:var(--stage);position:relative;font-family:"Montserrat",sans-serif}

  .card{position:absolute;left:280px;width:640px;height:370px;overflow:hidden;
        box-shadow:0 10px 30px rgba(0,0,0,.55)}

  /* Front: full name */
  .card--brand{top:55px;background:linear-gradient(180deg,var(--sky) 0%,var(--sky-soft) 30%,#b5a18c 65%,var(--amber-soft) 100%)}
  .brand-lockup{position:absolute;left:0;right:0;top:112px;text-align:center;color:var(--paper)}
  .brand-name{font-family:"Montserrat",sans-serif;font-weight:400;font-size:50px;letter-spacing:4px;line-height:1}
  .brand-rule{display:flex;align-items:center;justify-content:center;gap:14px;margin-top:18px}
  .brand-rule span{display:block;width:150px;height:2px;background:var(--paper)}
  .brand-tagline{font-family:"Josefin Sans",sans-serif;font-weight:300;font-size:18px;letter-spacing:9px;white-space:nowrap}

  /* Back: personal info */
  .card--contact{top:475px;background:linear-gradient(135deg,var(--paper) 55%,var(--paper-shade) 100%)}
  .card-band{position:absolute;inset:0;width:640px;height:370px}
  .holder{position:absolute;left:34px;top:22px;color:var(--paper)}
  .holder-name{font-weight:700;font-size:21px;letter-spacing:1.5px}
  .holder-role{font-weight:400;font-size:15px;margin-top:3px}

  .address{position:absolute;left:60px;top:160px;font-size:16px;font-weight:500;line-height:1.3;color:var(--ink)}
  .contact-list{position:absolute;left:34px;top:222px;list-style:none;font-size:16px;font-weight:500;color:var(--ink)}
  .contact-list li{display:flex;align-items:center;gap:12px;height:27px}
  .contact-list svg{width:17px;height:17px;fill:var(--amber);flex:none}

  .mark{position:absolute;right:40px;bottom:38px;display:flex;align-items:center;gap:10px}
  .mark-square{width:22px;height:22px;background:var(--amber)}
  .mark-name{font-weight:700;font-size:17px;color:var(--sky);letter-spacing:.5px}
</style>
</head>
<body>

<section class="card card--brand" aria-label="Card front">
  <div class="brand-lockup">
    <div class="brand-name">RW HOLLOWAY LLC</div>
    <div class="brand-rule"><span></span><div class="brand-tagline">CONSULTING ENGINEERS</div><span></span></div>
  </div>
</section>

<section class="card card--contact" aria-label="Card back">
  <svg class="card-band" viewBox="0 0 640 370" aria-hidden="true">
    <defs>
      <linearGradient id="warm-band" x1="0" y1="1" x2="1" y2="0">
        <stop offset="0" stop-color="#ee9633"/>
        <stop offset=".45" stop-color="#d99a55"/>
        <stop offset="1" stop-color="#7aa9d4"/>
      </linearGradient>
    </defs>
    <path d="M0 0H640V112C520 84 380 74 250 108C160 132 60 114 0 82Z" fill="#7aa9d4"/>
    <path d="M0 0H640V66C500 58 380 58 250 84C150 104 60 96 0 48Z" fill="url(#warm-band)"/>
    <path d="M0 48C60 96 150 104 250 84C380 58 500 58 640 66" fill="none" stroke="#ffffff" stroke-width="3"/>
    <path d="M300 152C400 112 510 96 615 112C520 100 410 112 302 162Z" fill="#a8a39a"/>
    <path d="M330 96C430 80 530 82 600 100" fill="none" stroke="#ffffff" stroke-width="2"/>
  </svg>

  <div class="holder">
    <div class="holder-name">DANA WHITFORD</div>
    <div class="holder-role">Co-Founder</div>
  </div>

  <address class="address">4810 Cedar Ridge Road<br>Suite 210 Lindale.14</address>

  <ul class="contact-list">
    <li><svg viewBox="0 0 24 24"><path d="M6.6 10.8a15 15 0 0 0 6.6 6.6l2.2-2.2a1 1 0 0 1 1-.25 11.4 11.4 0 0 0 3.6.57 1 1 0 0 1 1 1V20a1 1 0 0 1-1 1A17 17 0 0 1 3 4a1 1 0 0 1 1-1h3.5a1 1 0 0 1 1 1c0 1.25.2 2.45.57 3.57a1 1 0 0 1-.25 1z"/></svg>555-210-4471</li>
    <li><svg viewBox="0 0 24 24"><path d="M3 8c3-3 15-3 18 0v3h-5V9H8v2H3zM5 12h14l1 8H4zM10 14v4h4v-4z"/></svg>555-210-4482</li>
    <li><svg viewBox="0 0 24 24"><path d="M2 5h20v14H2zM4 7v.5l8 5 8-5V7l-8 5z"/></svg>info@rwhollowayllc</li>
    <li><svg viewBox="0 0 24 24"><circle cx="12" cy="12" r="10"/></svg>www.harlowmesa.com</li>
  </ul>

  <div class="mark">
    <span class="mark-square"></span>
    <span class="mark-name">RW Holloway LLC</span>
  </div>
</section>

</body>
</html>
```